verdant terraces simple classy business card design

my name is colin barrow and I run a gardening business aimed at high class verdant terraces. the business name is verdant terraces and our logo was designed on pixel harbour .My clientel are anything from residential homes to businesses. I take pride in my work and know that I offer a service like no other in my area.
The business card will be used to represent my business and I want it to be not only rememberable, but simplistic and modern. Eye catching too. Of course I would like it relatable to gardening and appealing to the correct clientel - those being garden enthusiasts, prestigious homes and businesses that are after top of the line gardening services like no other on the market.
I am not a typical lawn mowing business so I don't want a typical card design that represents that. The gardens I work with are generally million dollar properties with owners who are very garden proud looking for upkeep and guidance from me along with sometimes whole new garden designs. I want the business cards to show to my clients that I take pride, as they do, in their garden. And I want them to know from my card that I am a professional, qualified horticulturist offering them a top of the line service for life. I want them to refer my business on. I want them to look at my business card and see class and professionalism in a modern unique bold way.
The card should be simple with the possibility of the logo on the front being embossed/debossed and my details on the back the card should have a organic garden feel it's very important to me that it is absolutely perfect
I am also very open to ideas and suggestions so look forward to seeing the designs. the business logo has been supplied with this project and I want the card to be double sided

Contact info is
Colin Barrow - Managing Director / Horticulturist
Phone : 0481 526 704
Email: colinbarrow@verdantterraces.example.au

Target Market(s)

high class gardens residential and commercial

Industry/Entity Type

Gardener

Contact Information for Business Card

Contact info is
Phone : 0481 526 704

PLEASE MAKE CARD DOUBLE SIDED

Requirements
Must have
• organic simple classy modern feel
• must flow with the current logo that has been supplied with this project
• Double sided
• Must explain in a simple way that I deal with high end gardens and I'm a qualified horticulturist
Nice to have
• embossed debossed logo
Should not have
• shouldn't be to busy or cheap looking

```html
<!DOCTYPE html>
<html lang="en">
<head>
<meta charset="utf-8">
<title>Verdant Terraces – Business Card</title>
<link rel="stylesheet" href="https://fonts.googleapis.com/css2?family=Cinzel:wght@400&family=Source+Sans+3:wght@400&family=Tinos:wght@700&display=swap">
<style>
  :root {
    --page: #ffffff;
    --leaf-green: #629b52;
    --mark-green: #6aa25a;
    --night: #000000;
    --paper-white: #ffffff;
  }
  html, body {
    margin: 0;
    width: 1200px;
    height: 900px;
    overflow: hidden;
    background: var(--page);
  }
  .canvas { position: relative; width: 1200px; height: 900px; }
  .card {
    position: absolute;
    width: 477px;
    height: 294px;
    overflow: hidden;
  }
  .card--front {
    left: 116px; top: 275px;
    background: var(--leaf-green);
    border-radius: 0 46px 0 52px;
    color: var(--paper-white);
  }
  .card--back {
    left: 622px; top: 276px;
    height: 293px;
    background: var(--night);
    border-radius: 56px 0 56px 0;
  }
  .brand {
    position: absolute;
    text-align: center;
    font-family: "Cinzel", "Trajan Pro", serif;
    font-weight: 400;
    line-height: 1;
  }
  .brand__dot { display: block; margin: 0 auto; border-radius: 50%; }
  .brand__line { display: block; white-space: nowrap; }

  .card--front .brand { left: 211px; top: 37px; width: 241px; color: var(--paper-white); }
  .card--front .brand__dot { width: 62px; height: 62px; background: var(--paper-white); margin-bottom: 4px; }
  .card--front .brand__line--main { font-size: 32px; letter-spacing: 4px; margin-right: -4px; }
  .card--front .brand__line--sub { font-size: 16px; letter-spacing: 17px; margin-right: -17px; margin-top: 4px; }

  .card--back .brand { left: 97px; top: 77px; width: 282px; color: var(--mark-green); }
  .card--back .brand__dot { width: 82px; height: 82px; background: var(--mark-green); margin-bottom: 2px; }
  .card--back .brand__line--main { font-size: 38px; letter-spacing: 5px; margin-right: -5px; }
  .card--back .brand__line--sub { font-size: 19px; letter-spacing: 20px; margin-right: -20px; margin-top: 4px; }

  .person { position: absolute; left: 29px; top: 143px; }
  .person__name {
    font-family: "Tinos", "Times New Roman", serif;
    font-weight: 700; font-size: 18px; margin: 0; line-height: 1.1;
  }
  .person__role {
    font-family: "Source Sans 3", sans-serif;
    font-size: 13.5px; margin: 1px 0 0;
  }
  .divider {
    position: absolute; left: 0; right: 0; top: 197px;
    height: 1px; background: var(--paper-white);
  }
  .address, .contacts {
    position: absolute;
    font-family: "Source Sans 3", sans-serif;
    font-size: 13.5px; line-height: 17px; margin: 0; font-style: normal;
  }
  .address { left: 29px; top: 227px; }
  .contacts { right: 26px; top: 219px; list-style: none; padding: 0; text-align: right; }
  .contacts li { display: flex; align-items: center; justify-content: flex-end; gap: 5px; }
  .contacts svg { width: 9px; height: 9px; fill: var(--paper-white); }
</style>
</head>
<body>
<main class="canvas">
  <section class="card card--front" aria-label="Card front">
    <div class="brand">
      <span class="brand__dot"></span>
      <span class="brand__line brand__line--main">VERDANT</span>
      <span class="brand__line brand__line--sub">TERRACES</span>
    </div>
    <div class="person">
      <p class="person__name">Colin Barrow</p>
      <p class="person__role">Managing Director</p>
    </div>
    <div class="divider"></div>
    <address class="address">12345, Address Goes Here<br>Country Name, 123456.</address>
    <ul class="contacts">
      <li>0481 526 704
        <svg viewBox="0 0 10 10" aria-hidden="true"><path d="M2 0.5 L3.6 2.6 L2.7 3.8 Q3.6 5.8 6.2 7.3 L7.4 6.4 L9.5 8 L8.3 9.5 Q4.8 9.6 2.2 7 Q0 4.6 0.5 1.7 Z"/></svg>
      </li>
      <li>info@verdantterraces.example
        <svg viewBox="0 0 10 10" aria-hidden="true"><path d="M0.5 2 H9.5 V8 H0.5 Z M0.5 2 L5 5.5 L9.5 2" stroke="#629b52" stroke-width="0.8"/></svg>
      </li>
      <li>www.verdantterraces.example
        <svg viewBox="0 0 10 10" aria-hidden="true"><circle cx="5" cy="5" r="4.5"/><path d="M0.5 5 H9.5 M5 0.5 V9.5 M1.5 2.8 H8.5 M1.5 7.2 H8.5" stroke="#629b52" stroke-width="0.6" fill="none"/></svg>
      </li>
    </ul>
  </section>
  <section class="card card--back" aria-label="Card back">
    <div class="brand">
      <span class="brand__dot"></span>
      <span class="brand__line brand__line--main">VERDANT</span>
      <span class="brand__line brand__line--sub">TERRACES</span>
    </div>
  </section>
</main>
</body>
</html>
```